Bespoke Builders Business Card Design

We need a business card for an established builder of high quality bespoke homes in Auckland and Northland. We build and renovate homes collaboratively facilitating effective communication between owners, builders, architects, suppliers and tradespeople. We have never built or renovated a home that leaks or has faults. We only use reliable materials. We have never been sued or had legal action taken against us. We are honest builders of bespoke homes not group mass produced homes. Our niche market is in character homes. We practice sustainability and have built a lot of coastal property. We have been in business for over thirty years . We would like to see natural colors of the environment sand,sea and maybe vegetation . The design should communicate quality, sustainability,fair pricing, open communication and the originality of bespoke building. And the fact that the builder is registered.

Industry/Entity Type

Business

Contact Information for Business Card

Rowan Tellick Builders
Ph. 021583917
18 Kestrel Rd Harwood Bay Auckland 0814
PO Box 927 Mangawhai 0583

```html
<!DOCTYPE html>
<html lang="en">
<head>
<meta charset="utf-8">
<title>Rowan Tellick Builders – Business Card</title>
<link href="https://fonts.googleapis.com/css2?family=PT+Serif&family=Open+Sans:wght@400&display=swap" rel="stylesheet">
<style>
  :root {
    --canvas-bg: #e9e7e3;
    --card-bg: #ffffff;
    --card-shade: #e9e9e9;
    --brand-red: #8e1b1b;
    --ink: #161616;
    --rule: #111111;
    --timber: #c29a6b;
    --render: #eef0f1;
    --roof: #5a5d60;
  }
  * { box-sizing: border-box; margin: 0; padding: 0; }
  html, body {
    width: 1200px; height: 892px; overflow: hidden;
    background: var(--canvas-bg);
  }
  .canvas {
    width: 1200px; height: 892px;
    display: flex; flex-direction: column; align-items: center; justify-content: center;
    gap: 30px;
  }
  .card {
    position: relative;
    width: 620px; height: 400px;
    background: radial-gradient(ellipse at 50% 40%, var(--card-bg) 55%, var(--card-shade) 100%);
    box-shadow: 0 4px 14px rgba(0,0,0,0.18);
    overflow: hidden;
  }

  /* Front face */
  .card-front__title {
    position: absolute; left: 0; right: 0; top: 58px;
    display: flex; align-items: flex-end;
  }
  .card-front__rule {
    flex: 1; height: 3px; background: var(--rule); margin-bottom: 6px;
  }
  .card-front__rule--left { flex: 0 0 70px; }
  .card-front__name {
    font-family: "PT Serif", serif;
    font-weight: 400;
    font-size: 38px; line-height: 1; color: var(--brand-red);
    padding: 0 16px; white-space: nowrap; letter-spacing: 0.3px;
  }
  .card-front__contact {
    position: absolute; left: 0; right: 0; top: 128px;
    text-align: center;
    font-family: "Open Sans", sans-serif;
    font-style: normal;
    font-size: 16px; line-height: 26px; color: var(--ink);
  }
  .card-front__house {
    position: absolute; left: 260px; top: 222px;
    width: 200px; height: 150px;
    background:
      linear-gradient(160deg, var(--roof) 0%, var(--roof) 18%, var(--timber) 30%, var(--timber) 45%, var(--render) 58%, #fafafa 100%);
    clip-path: polygon(8% 40%, 45% 6%, 96% 30%, 96% 86%, 55% 100%, 8% 78%);
  }

  /* Back face */
  .card-back__house {
    position: absolute; left: 110px; top: 70px;
    width: 300px; height: 270px;
    background: linear-gradient(150deg, #eadfcf 0%, #ece8e2 40%, #f3f3f3 100%);
    clip-path: polygon(6% 38%, 48% 4%, 96% 28%, 96% 84%, 52% 100%, 6% 80%);
    opacity: 0.8;
  }
  .card-back__name {
    position: absolute; left: 0; right: 0; top: 170px;
    text-align: center;
    font-family: "PT Serif", serif;
    font-weight: 400;
    font-size: 40px; line-height: 1.2; color: var(--ink);
    white-space: nowrap;
  }
</style>
</head>
<body>
<main class="canvas">
  <section class="card card-front" aria-label="Business card front">
    <div class="card-front__title">
      <span class="card-front__rule card-front__rule--left"></span>
      <h1 class="card-front__name">Rowan Tellick Builders</h1>
      <span class="card-front__rule"></span>
    </div>
    <address class="card-front__contact">
      <div class="phone">021583917</div>
      <div>18 Kestrel Rd Harwood Bay Auckland 0814</div>
      <div>PO Box 927 Mangawhai 0583</div>
    </address>
    <div class="card-front__house" role="img" aria-label="Illustration of a two-storey house under construction with timber roof framing"></div>
  </section>

  <section class="card card-back" aria-label="Business card back">
    <div class="card-back__house" role="img" aria-label="Faint illustration of a house under construction"></div>
    <p class="card-back__name">Rowan Tellick Builders</p>
  </section>
</main>
</body>
</html>
```